Professional looking Roller Blind Discount Card that portrays quality at a value for money price!

We need a double sided business card designed as a discount card. Size 90mm wide x 55mm high.We would like it to look professional and portray quality at a value for money price point.I have uploaded a word document with a basic layout with the information we want included on each side of the card. Please put your own thought into the layout.

Contact Information for Business Card

As per word document attached.

```html
<!DOCTYPE html>
<html lang="en">
<head>
<meta charset="utf-8">
<title>Brightwater Blinds – Roller Blind Discount Card</title>
<link rel="stylesheet" href="https://fonts.googleapis.com/css2?family=Arimo:wght@400;700&display=swap">
<style>
  :root{
    --bg:#d6d6d6;
    --card:#ffffff;
    --blue:#2aa7df;
    --grey:#6d6e70;
    --brown:#6e5a4f;
    --gold:#e8a81c;
    --gold-light:#f7cf4a;
    --white:#ffffff;
  }
  *{box-sizing:border-box;margin:0;padding:0}
  html,body{width:1200px;height:900px;overflow:hidden}
  body{
    background:var(--bg);
    font-family:"Arimo",Arial,sans-serif;
    display:flex;flex-direction:column;align-items:center;justify-content:center;gap:38px;
  }
  .card{
    position:relative;width:640px;height:391px;overflow:hidden;
    box-shadow:0 4px 14px rgba(0,0,0,.18);
  }

  /* ---------- front ---------- */
  .card--front{background:var(--card)}
  .front__content{position:absolute;left:56px;top:66px}
  .brand-name{font-family:"Arimo",Arial,sans-serif;font-weight:400;line-height:1}
  .front__content .brand-name{color:var(--blue);font-size:36px}
  .offer{color:var(--blue);font-weight:700;font-size:42px;margin-top:18px;line-height:1}
  .offer-detail{color:var(--grey);font-size:19px;line-height:1.3;margin-top:10px}
  .offer-detail .dot{color:var(--blue)}
  .badges{display:flex;gap:16px;margin-top:14px}
  .call{color:var(--grey);font-size:21px;margin-top:14px}
  .call strong{color:var(--blue)}
  .brand-square{position:absolute;right:54px;top:54px;width:60px;height:60px;background:var(--blue)}
  .front__rule{position:absolute;left:0;right:0;bottom:22px;height:8px;background:var(--grey)}
  .front__rule--blue{bottom:10px;height:4px;background:var(--blue)}

  /* ---------- back ---------- */
  .back__photo{
    position:absolute;inset:0;
    background:linear-gradient(135deg,#8c7a6c 0%,#9ba88a 35%,#5f7f4e 60%,#c9c4b6 100%);
  }
  .back__brand{
    position:absolute;left:0;top:0;width:260px;height:140px;
    background:rgba(110,90,79,.88);
    display:flex;align-items:center;justify-content:center;
  }
  .back__brand .brand-name{color:var(--white);font-size:24px}
  .back__banner{
    position:absolute;left:260px;right:0;top:0;height:140px;background:var(--blue);
    display:flex;flex-direction:column;align-items:flex-end;justify-content:center;padding-right:30px;gap:12px;
  }
  .banner__title{
    background:var(--grey);color:var(--white);font-size:32px;padding:6px 14px;letter-spacing:1px;
  }
  .banner__sub{color:var(--white);font-size:24px}
  .back__cta{
    position:absolute;left:400px;right:0;top:140px;bottom:0;
    background:rgba(110,90,79,.9);border-left:4px solid var(--blue);
    display:flex;flex-direction:column;justify-content:center;padding-left:26px;gap:8px;
    color:var(--white);
  }
  .cta__label{font-size:26px;letter-spacing:1px}
  .cta__phone{font-size:30px;font-weight:700}
</style>
</head>
<body>

  <section class="card card--front" aria-label="Discount card front">
    <div class="brand-square" aria-hidden="true"></div>
    <div class="front__content">
      <h1 class="brand-name">Brightwater Blinds</h1>
      <p class="offer">25% OFF</p>
      <p class="offer-detail">Quality Custom Made Roller Blinds<br>
        Blockout <span class="dot">•</span> Screen <span class="dot">•</span> Light Filtering</p>
      <div class="badges" aria-label="Best price guarantee seals">
        <svg width="52" height="52" viewBox="0 0 52 52" aria-hidden="true"><circle cx="26" cy="26" r="25" fill="var(--gold)"/><circle cx="26" cy="26" r="18" fill="var(--gold-light)"/></svg>
        <svg width="52" height="52" viewBox="0 0 52 52" aria-hidden="true"><circle cx="26" cy="26" r="25" fill="var(--gold)"/><circle cx="26" cy="26" r="18" fill="var(--gold-light)"/></svg>
        <svg width="52" height="52" viewBox="0 0 52 52" aria-hidden="true"><circle cx="26" cy="26" r="25" fill="var(--gold)"/><circle cx="26" cy="26" r="18" fill="var(--gold-light)"/></svg>
      </div>
      <p class="call">Call <strong>0400 123 456</strong> Today!</p>
    </div>
    <div class="front__rule"></div>
    <div class="front__rule front__rule--blue"></div>
  </section>

  <section class="card card--back" aria-label="Discount card back">
    <div class="back__photo" role="img" aria-label="Photo of a room with roller blinds over large windows looking onto a garden"></div>
    <div class="back__brand"><span class="brand-name">Brightwater Blinds</span></div>
    <div class="back__banner">
      <span class="banner__title">ROLLER BLINDS</span>
      <span class="banner__sub">Huge Selection of Fabrics</span>
    </div>
    <div class="back__cta">
      <span class="cta__label">CALL TODAY!</span>
      <span class="cta__phone">0400 123 456</span>
    </div>
  </section>

</body>
</html>
```